indépendant en tant que Massothérapeute et Préparateur Mental, j'ai besoin de ...

Massothérapeute et préparateur mental indépendant, je recherche une carte de visite sobre et dynamique, sans images liées au massage ou à la préparation mentale mais intégrant mon logo. Les couleurs que j'aime bien sont : Blanc, gris, anthracite, noir et jaune

Contact Information for Business Card

carte de préférence Horizontale
neutre qui puisse toucher le deux domaines Massothérapie et préparation mentale

Requirements
Must have
• mon projet doit intégrer au recto:
LOGO
Loïc Bardèze
078 513 26 48
info@loicbardeze.ch
et éventuellement www.loicbardeze.ch

et au verso les deux adresses:

Chemin des Ormilles 7B
1400 Yverdon-les-Bains

Route de la Gravière 9
1700 Fribourg

Should not have
• mon projet ne doit pas contenir d'image en liens avec le massage ni la préparation mentale.

```html
<!DOCTYPE html>
<html lang="fr">
<head>
<meta charset="utf-8">
<title>Carte de visite – Loïc Bardèze</title>
<link rel="stylesheet" href="https://fonts.googleapis.com/css2?family=Lato:wght@400;700;900&display=swap">
<style>
  :root {
    --yellow: #fdbf17;
    --paper: #ffffff;
    --ink: #111111;
    --grey-line: #b8b8b8;
    --backdrop: #e6e6e6;
    --frame: 17px;
  }
  * { box-sizing: border-box; margin: 0; padding: 0; }
  html, body {
    width: 1200px; height: 801px; overflow: hidden;
    background: var(--backdrop);
    font-family: "Lato", sans-serif;
    color: var(--ink);
  }
  .stage { position: relative; width: 1200px; height: 801px; }

  .card {
    position: absolute; left: 354px; width: 516px; height: 309px;
    background: var(--paper);
  }
  .card--back { top: 46px; }
  .card--front { top: 424px; }

  /* Back: yellow bracket on the left half */
  .bracket {
    position: absolute; left: 0; top: 0; width: 258px; height: 100%;
    border: var(--frame) solid var(--yellow); border-right: none;
  }
  .side-tab {
    position: absolute; right: 0; top: 147px; width: 34px; height: 17px;
    background: var(--yellow);
  }
  .addresses {
    position: absolute; left: 29px; top: 143px;
    display: flex; align-items: center;
    font-size: 11.5px; line-height: 16px; letter-spacing: 0.2px;
  }
  .pin { width: 14px; height: 19px; margin-right: 7px; }
  .slash { width: 16px; height: 28px; margin: 0 8px; }
  .back-mark {
    position: absolute; right: 48px; top: 149px;
    font-weight: 900; font-size: 11px; letter-spacing: 0.3px;
  }

  /* Front: full yellow frame */
  .frame {
    position: absolute; inset: 0;
    border: var(--frame) solid var(--yellow);
  }
  .holder-name {
    position: absolute; left: 42px; top: 162px;
    font-weight: 700; font-size: 17px; letter-spacing: 1.6px;
    text-transform: uppercase;
  }
  .contact-list {
    position: absolute; left: 44px; top: 203px;
    list-style: none; font-size: 13.5px; line-height: 22px; letter-spacing: 0.5px;
  }
  .contact-list b { font-weight: 700; display: inline-block; width: 22px; }
  .brand {
    position: absolute; left: 258px; top: 230px;
    display: flex; align-items: center; gap: 7px;
  }
  .brand-square { width: 12px; height: 12px; background: var(--ink); }
  .brand-name { font-weight: 900; font-size: 15px; letter-spacing: 0.4px; }
  .brand-role { position: absolute; left: 19px; top: 20px; font-size: 6.5px; white-space: nowrap; letter-spacing: 0.3px; }
</style>
</head>
<body>
<main class="stage">

  <section class="card card--back" aria-label="Verso">
    <div class="bracket"></div>
    <div class="side-tab"></div>
    <div class="addresses">
      <svg class="pin" viewBox="0 0 14 19" aria-hidden="true">
        <path d="M7 0C3.1 0 0 3 0 6.8 0 11.6 7 19 7 19s7-7.4 7-12.2C14 3 10.9 0 7 0zm0 9.5a2.7 2.7 0 1 1 0-5.4 2.7 2.7 0 0 1 0 5.4z" fill="#111"/>
      </svg>
      <address class="address" style="font-style:normal">Chemin des Ormilles 7B<br>1400 Yverdon-les-Bains</address>
      <svg class="slash" viewBox="0 0 16 28" aria-hidden="true">
        <line x1="14" y1="1" x2="2" y2="27" stroke="#9a9a9a" stroke-width="1"/>
      </svg>
      <address class="address" style="font-style:normal">Route de la Gravière 9<br>1700 Fribourg</address>
    </div>
    <div class="back-mark">Loïc Bardèze</div>
  </section>

  <section class="card card--front" aria-label="Recto">
    <div class="frame"></div>
    <h1 class="holder-name">Loïc Bardèze</h1>
    <ul class="contact-list">
      <li><b>M</b>: 078 513 26 48</li>
      <li><b>E</b>: info@loicbardeze.ch</li>
      <li><b>W</b>: www.loicbardeze.ch</li>
    </ul>
    <div class="brand">
      <span class="brand-square"></span>
      <span class="brand-name">Loïc Bardèze</span>
      <span class="brand-role">Massothérapeute / Préparateur Mental</span>
    </div>
  </section>

</main>
</body>
</html>
```